Bluecrest Learning Corps by graduating students from college in two years

Based on the logo design, create stationary and business cards for
Dr. Venrel T Oskamp, CEO, (703) 482-1736
and Marisa Deltoft, Respresentative, (301) 647-2208
Address: 4719 Pellham Court, Marrowfield, VA 22187
Incorporate elelments of the logo

Target Market(s)

USA

Font styles to use
Other font styles liked:
• match with the logo type style

```html
<!DOCTYPE html>
<html lang="en">
<head>
<meta charset="utf-8">
<title>Bluecrest Learning Corps – Stationery</title>
<link rel="stylesheet" href="https://fonts.googleapis.com/css2?family=Libre+Baskerville:ital,wght@0,400;0,700;1,400&family=Tinos:wght@400;700&family=Roboto+Condensed:wght@300;400;700&display=swap">
<style>
  :root {
    --navy: #252f6b;
    --navy-deep: #232b63;
    --gold: #fbc52f;
    --stage: #d5dadd;
    --paper: #ffffff;
    --lavender: #b8b7d0;
    --ink: #1d1d24;
    --label: #f4f5f6;
  }
  * { box-sizing: border-box; margin: 0; padding: 0; }
  html, body { width: 1200px; height: 916px; overflow: hidden; }
  body {
    position: relative;
    background: radial-gradient(ellipse at 50% 30%, #e1e5e7 0%, var(--stage) 70%, #c9cfd2 100%);
    font-family: "Tinos", "Times New Roman", serif;
    color: var(--navy);
  }
  .icon-defs { position: absolute; width: 0; height: 0; }
  .icon { width: 9px; height: 9px; fill: var(--gold); flex: none; }

  /* ---------- Business cards ---------- */
  .card {
    position: absolute;
    left: 68px;
    width: 437px;
    height: 249px;
    box-shadow: 0 6px 10px rgba(0,0,0,0.28);
  }
  .card--front {
    top: 66px;
    background: radial-gradient(circle at 50% 50%, #323d7d 0%, var(--navy-deep) 75%);
    display: flex;
    align-items: center;
    justify-content: center;
  }
  .card--front .brand-name {
    font-family: "Libre Baskerville", serif;
    font-weight: 700;
    font-size: 18px;
    color: var(--gold);
    text-align: center;
    line-height: 1.35;
    letter-spacing: 0.5px;
  }
  .card--back { background: var(--paper); }
  .card--ceo { top: 339px; }
  .card--rep { top: 614px; }

  .card__brand {
    position: absolute;
    left: 45px;
    top: 55px;
    width: 130px;
    height: 130px;
    display: flex;
    flex-direction: column;
    align-items: center;
    justify-content: center;
    gap: 8px;
  }
  .brand-dot {
    width: 16px; height: 16px; border-radius: 50%;
    background: var(--gold);
  }
  .card__brand .brand-name {
    font-family: "Libre Baskerville", serif;
    font-weight: 700;
    font-size: 13px;
    line-height: 1.35;
    color: var(--navy);
    text-align: center;
  }
  .card__divider {
    position: absolute;
    left: 219px; top: 43px;
    width: 1px; height: 162px;
    background: var(--gold);
  }
  .card__info {
    position: absolute;
    left: 255px; top: 60px;
    font-size: 11.5px;
    letter-spacing: 0.4px;
    color: var(--navy);
  }
  .card__name {
    font-family: "Libre Baskerville", serif;
    font-weight: 700;
    font-size: 15.5px;
    color: var(--gold);
    letter-spacing: 0.3px;
    line-height: 1.1;
    white-space: nowrap;
  }
  .card__role { font-size: 12px; margin-top: 2px; }
  .card__address { margin-top: 12px; line-height: 15px; }
  .card__contacts { margin-top: 10px; list-style: none; line-height: 15px; }
  .card__contacts li { display: flex; align-items: center; gap: 7px; }

  /* ---------- Letterhead ---------- */
  .letterhead {
    position: absolute;
    left: 563px; top: 66px;
    width: 558px; height: 787px;
    background: var(--paper);
    box-shadow: 0 6px 12px rgba(0,0,0,0.2);
    overflow: hidden;
  }
  .lh__brand {
    position: absolute;
    left: 28px; top: 30px;
    width: 76px; height: 76px;
    display: flex; flex-direction: column;
    align-items: center; justify-content: center; gap: 4px;
  }
  .lh__brand .brand-dot { width: 10px; height: 10px; }
  .lh__brand .brand-name {
    font-family: "Libre Baskerville", serif;
    font-weight: 700; font-size: 8.5px; line-height: 1.3;
    text-align: center; color: var(--navy);
  }
  .lh__contacts {
    position: absolute;
    right: 33px; top: 37px;
    list-style: none;
    font-size: 11.2px;
    line-height: 15px;
    color: var(--navy);
    text-align: right;
  }
  .lh__contacts li { display: flex; justify-content: flex-end; align-items: center; gap: 8px; }
  .lh__rule {
    position: absolute; top: 117px; left: 28px; width: 499px; height: 3px;
    display: flex; align-items: flex-start;
  }
  .lh__rule-navy { width: 235px; height: 1px; background: var(--navy); margin-top: 1px; }
  .lh__rule-gold { flex: 1; height: 3px; background: var(--gold); }

  .lh__sender { position: absolute; left: 29px; top: 158px; }
  .person-name {
    font-family: "Roboto Condensed", sans-serif;
    font-size: 27px; line-height: 1;
    font-weight: 400;
    color: var(--navy);
  }
  .person-name .first { font-weight: 700; color: var(--gold); }
  .person-role { font-size: 10.5px; color: var(--ink); margin-top: 5px; margin-left: 1px; }
  .lh__date {
    position: absolute; right: 42px; top: 168px;
    font-size: 13px; color: var(--ink);
  }
  .lh__direct {
    position: absolute; left: 29px; top: 216px;
    list-style: none; font-size: 10.5px; line-height: 13px; color: var(--ink);
  }
  .lh__direct li { display: flex; align-items: center; gap: 6px; }
  .lh__body {
    position: absolute; left: 29px; top: 279px; width: 498px;
    font-size: 11.4px; line-height: 16px; color: var(--ink);
    text-align: justify;
  }
  .lh__body p + p { margin-top: 15.5px; }
  .lh__signature {
    position: absolute; left: 29px; top: 557px;
    width: 190px; height: 58px;
    background: linear-gradient(90deg, #eeeef2, #f7f7f9);
  }
  .lh__signer { position: absolute; left: 29px; top: 620px; }
  .lh__signer .person-role { margin-top: 6px; }
  .lh__emblem {
    position: absolute; left: 223px; top: 572px;
    width: 335px; height: 215px;
    background: linear-gradient(160deg, rgba(184,183,208,0.35) 0%, var(--lavender) 65%);
  }

  /* ---------- Captions ---------- */
  .caption {
    position: absolute;
    font-family: "Libre Baskerville", serif;
    font-style: italic;
    font-size: 30px;
    color: var(--label);
    letter-spacing: 1.5px;
    text-shadow: 0 2px 3px rgba(0,0,0,0.35);
    transform: translateX(-50%);
    white-space: nowrap;
  }
  .caption--cards { left: 248px; top: 870px; }
  .caption--letter { left: 847px; top: 865px; }
</style>
</head>
<body>

<svg class="icon-defs" aria-hidden="true">
  <symbol id="i-phone" viewBox="0 0 24 24"><path d="M6.6 10.8a15.1 15.1 0 0 0 6.6 6.6l2.2-2.2c.3-.3.7-.4 1-.2 1.1.4 2.3.6 3.6.6.6 0 1 .4 1 1V20c0 .6-.4 1-1 1C10.6 21 3 13.4 3 4c0-.6.4-1 1-1h3.5c.6 0 1 .4 1 1 0 1.3.2 2.5.6 3.6.1.3 0 .7-.2 1z"/></symbol>
  <symbol id="i-globe" viewBox="0 0 24 24"><path d="M12 2a10 10 0 1 0 0 20 10 10 0 0 0 0-20zm-1 17.9A8 8 0 0 1 4.2 10.8L9 15.6v1a2 2 0 0 0 2 2zm6.9-2.5A2 2 0 0 0 16 16h-1v-3a1 1 0 0 0-1-1H8v-2h2a1 1 0 0 0 1-1V7h2a2 2 0 0 0 2-2v-.4a8 8 0 0 1 2.9 12.8z"/></symbol>
  <symbol id="i-mail" viewBox="0 0 24 24"><path d="M3 5h18a1 1 0 0 1 1 1v12a1 1 0 0 1-1 1H3a1 1 0 0 1-1-1V6a1 1 0 0 1 1-1zm1 2.5V17h16V7.5l-8 5.5z"/></symbol>
  <symbol id="i-pin" viewBox="0 0 24 24"><path d="M12 2a7 7 0 0 0-7 7c0 5.2 7 13 7 13s7-7.8 7-13a7 7 0 0 0-7-7zm0 9.5a2.5 2.5 0 1 1 0-5 2.5 2.5 0 0 1 0 5z"/></symbol>
</svg>

<!-- Business cards -->
<section class="card card--front">
  <p class="brand-name">Bluecrest<br>Learning Corps</p>
</section>

<section class="card card--back card--ceo">
  <div class="card__brand">
    <span class="brand-dot"></span>
    <p class="brand-name">Bluecrest<br>Learning<br>Corps</p>
  </div>
  <div class="card__divider"></div>
  <div class="card__info">
    <h2 class="card__name">Dr. Venrel T Oskamp</h2>
    <p class="card__role">CEO</p>
    <p class="card__address">4719 Pellham Court,<br>Marrowfield, VA 22187</p>
    <ul class="card__contacts">
      <li><svg class="icon"><use href="#i-phone"/></svg>(703) 482-1736</li>
      <li><svg class="icon"><use href="#i-globe"/></svg>www.bluecrestcorps.org</li>
      <li><svg class="icon"><use href="#i-mail"/></svg>info@bluecrestcorps.org</li>
    </ul>
  </div>
</section>

<section class="card card--back card--rep">
  <div class="card__brand">
    <span class="brand-dot"></span>
    <p class="brand-name">Bluecrest<br>Learning<br>Corps</p>
  </div>
  <div class="card__divider"></div>
  <div class="card__info">
    <h2 class="card__name">Marisa Deltoft</h2>
    <p class="card__role">Respresentative</p>
    <p class="card__address">4719 Pellham Court,<br>Marrowfield, VA 22187</p>
    <ul class="card__contacts">
      <li><svg class="icon"><use href="#i-phone"/></svg>(301) 647-2208</li>
      <li><svg class="icon"><use href="#i-globe"/></svg>www.bluecrestcorps.org</li>
      <li><svg class="icon"><use href="#i-mail"/></svg>info@bluecrestcorps.org</li>
    </ul>
  </div>
</section>

<!-- Letterhead -->
<article class="letterhead">
  <div class="lh__brand">
    <span class="brand-dot"></span>
    <p class="brand-name">Bluecrest<br>Learning<br>Corps</p>
  </div>
  <ul class="lh__contacts">
    <li>(301) 647-2208<svg class="icon"><use href="#i-phone"/></svg></li>
    <li>www.bluecrestcorps.org<svg class="icon"><use href="#i-globe"/></svg></li>
    <li>info@bluecrestcorps.org<svg class="icon"><use href="#i-mail"/></svg></li>
    <li>4719 Pellham Court, Marrowfield, VA 22187<svg class="icon"><use href="#i-pin"/></svg></li>
  </ul>
  <div class="lh__rule"><span class="lh__rule-navy"></span><span class="lh__rule-gold"></span></div>

  <div class="lh__sender">
    <h1 class="person-name"><span class="first">Corvina</span> Maltrey</h1>
    <p class="person-role">Founder &amp; CEO</p>
  </div>
  <p class="lh__date">August-05-2019</p>
  <ul class="lh__direct">
    <li><svg class="icon"><use href="#i-phone"/></svg>(817) 530-4162</li>
    <li><svg class="icon"><use href="#i-globe"/></svg>www.bluecrestcorps.org</li>
    <li><svg class="icon"><use href="#i-mail"/></svg>info@bluecrestcorps.org</li>
  </ul>

  <div class="lh__body">
    <p>Lorem ipsum dolor sit amet, consectetuer adipiscing elit, sed diam nonummy nibh euismod tincidunt ut laoreet dolore magna aliquam erat volutpat. Ut wisi enim ad minim veniam, quis nostrud exerci tation ullamcorper suscipit lobortis</p>
    <p>Lorem ipsum dolor sit amet, cons ectetuer adipiscing elit, sed diam nonummy nibh euismod tincidunt ut laoreet dolore magna aliquam erat volutpat. Ut wisi enim ad minim veniam, quis nostrud exerci tation ullamcorper suscipit lobortis nisl ut aliquip ex ea commodo consequat. Lorem ipsum dolor sit amet, consectetuer olutpat. Ut wisi enim ad minim veniam, quis nostrud exerci tation ullamcorper suscipit lobortis nisl ut aliquip ex ea commodo consequat. Duis autem</p>
    <p>vel eum iriure dolor in hendrerit in vulputate velit esse molestie consequat, vel illum dolore eu feugiat nulla facilisis at vero eros et accumsan et iusto odio dignissim qui blandit praesent luptatum zzril delenit augue duis dolore te feugait nulla facilisi. Lorem ipsum dolor sit amet, cons ectetuer adipiscing elit, sed diam nonummy nibh euismod tincidunt ut laoreet dolore magna aliquam erat volutpat. Ut wisi enim .</p>
  </div>

  <div class="lh__signature" role="img" aria-label="Handwritten signature of the director"></div>
  <div class="lh__signer">
    <h2 class="person-name"><span class="first">Ansel</span> Pryderi</h2>
    <p class="person-role">Director</p>
  </div>
  <div class="lh__emblem" role="img" aria-label="Large lavender graduation cap illustration with tassel"></div>
</article>

<p class="caption caption--cards">Business card</p>
<p class="caption caption--letter">A4 Letterhead</p>

</body>
</html>
```